Corvane Freight Company Business Card Design

We are a company that delivers natural saltwater (from the ocean) to aquarium companies, restaurants and home marine tanks. I would like a new business card to suit.

Must include Name, company name, abn, contact number and website as well as logo (see attached).

Looking for a design that stands out, has a clean but unique appearance.

Double and single sided entries welcome

Business

• Logo

```html
<!DOCTYPE html>
<html lang="en">
<head>
<meta charset="utf-8">
<title>Corvane Freight Company Business Card</title>
<link rel="stylesheet" href="https://fonts.googleapis.com/css2?family=Open+Sans:wght@400;600;700&display=swap">
<style>
  :root {
    --backdrop: #2f2622;
    --card-white: #ffffff;
    --brand-blue: #0b5cab;
    --brand-sky: #1b93d8;
    --accent-sky: #5bc8f2;
    --ink: #2b2b2b;
    --on-blue: #ffffff;
  }
  * { box-sizing: border-box; margin: 0; padding: 0; }
  html, body {
    width: 1200px; height: 471px; overflow: hidden;
    background: var(--backdrop);
    font-family: "Open Sans", Arial, sans-serif;
  }
  .canvas { position: relative; width: 1200px; height: 471px; }

  .card {
    position: absolute; top: 74px; width: 525px; height: 299px;
    border-radius: 15px; overflow: hidden;
  }
  .card--front { left: 39px; background: var(--card-white); }
  .card--back { left: 628px; background: var(--brand-blue); border: 1px solid #d8e4f2; }

  .wordmark { font-weight: 600; line-height: 1; letter-spacing: -0.5px; }
  .card--front .wordmark {
    position: absolute; left: 28px; top: 68px;
    color: var(--brand-sky); font-size: 36px;
  }
  .card--front .wordmark .wordmark__sub { display: block; font-size: 22px; margin-top: 6px; }

  .card--back .wordmark {
    position: absolute; left: 0; right: 0; top: 116px; text-align: center;
    color: var(--on-blue); font-size: 52px;
  }
  .card--back .wordmark .wordmark__sub { display: block; font-size: 28px; margin-top: 10px; }

  .name-band {
    position: absolute; left: 0; top: 167px; width: 487px; height: 29px;
    background: var(--brand-blue); color: var(--on-blue);
    padding-left: 27px; display: flex; align-items: center; font-size: 15px;
  }
  .name-band__name { font-weight: 700; font-size: 16px; margin-right: 5px; }
  .name-band__tab {
    position: absolute; left: 490px; top: 167px; width: 35px; height: 29px;
    background: var(--accent-sky);
  }

  .contact {
    position: absolute; left: 27px; top: 203px;
    color: var(--ink); font-size: 12.5px; line-height: 21px; list-style: none;
  }
  .contact__item { display: flex; align-items: center; gap: 7px; }
  .contact__item svg { width: 10px; height: 10px; }
  .contact__item--gap { margin-top: 2px; }
</style>
</head>
<body>
<div class="canvas">
  <section class="card card--front" aria-label="Card front">
    <div class="wordmark">Corvane Freight<span class="wordmark__sub">Company</span></div>
    <div class="name-band"><span class="name-band__name">Your Name,</span> Title</div>
    <div class="name-band__tab"></div>
    <ul class="contact">
      <li class="contact__item">
        <svg viewBox="0 0 10 10" aria-hidden="true"><path d="M2 1 L3.6 1 L4.2 3 L3.2 3.8 Q4.2 5.8 6.2 6.8 L7 5.8 L9 6.4 L9 8 Q8.5 9 7.5 9 Q1 8 1 2.5 Q1 1.5 2 1Z" fill="#2b2b2b"/></svg>
        123-456-7892
      </li>
      <li class="contact__item">
        <svg viewBox="0 0 10 10" aria-hidden="true"><circle cx="5" cy="5" r="4.2" fill="none" stroke="#2b2b2b" stroke-width="1"/><ellipse cx="5" cy="5" rx="1.8" ry="4.2" fill="none" stroke="#2b2b2b" stroke-width="0.8"/><line x1="0.8" y1="5" x2="9.2" y2="5" stroke="#2b2b2b" stroke-width="0.8"/></svg>
        www.corvanefreight.com
      </li>
      <li class="contact__item contact__item--gap">Street Name, City Name ,State, Zip Code</li>
      <li class="contact__item">ABN: 123456789</li>
    </ul>
  </section>

  <section class="card card--back" aria-label="Card back">
    <div class="wordmark">Corvane Freight<span class="wordmark__sub">Company</span></div>
  </section>
</div>
</body>
</html>
```